Business Card Design for company

We want new business cards. We'd like something different-- yet still highly professional. Our tagline is Providing leadership, delivering success. Stock photos are ok, as long as they are relevant and look upscale.

Target Market(s)

Architecture/Business Management Consulting/Engineering Consulting

Contact Information for Business Card

dark gray background with pops of blue might be good, but you tell me. You're the designers. Rounded corners might be nice, but again, you tell me.

Font styles to use
Serif
Sans Serif

Colors
3276b5
5c5c5c
9d9d9d
fbfbfb

Requirements
Nice to have
• Something different, but still very professional.

```html
<!DOCTYPE html>
<html lang="en">
<head>
<meta charset="utf-8">
<title>Vantore Global – Business Card</title>
<link href="https://fonts.googleapis.com/css2?family=Montserrat:wght@400;500;700&family=Arimo:wght@400;700&display=swap" rel="stylesheet">
<style>
  :root {
    --blue: #3276b5;
    --blue-deep: #2a57a8;
    --graphite: #45474c;
    --graphite-dark: #3a3c40;
    --grey: #5c5c5c;
    --grey-light: #9d9d9d;
    --paper: #fbfbfb;
    --stage: #e4e5e7;
  }
  * { margin: 0; padding: 0; box-sizing: border-box; }
  html, body { width: 1200px; height: 900px; overflow: hidden; }
  body {
    background: var(--stage);
    font-family: "Arimo", Arial, sans-serif;
    position: relative;
  }
  .card {
    position: absolute;
    left: 267px;
    width: 666px;
    height: 380px;
    overflow: hidden;
    box-shadow: 0 6px 18px rgba(0,0,0,.18);
  }
  /* Front */
  .card--front { top: 50px; background: var(--graphite); }
  .front__map {
    position: absolute; left: 40px; top: 30px; width: 586px; height: 250px;
    background: radial-gradient(ellipse at 50% 50%, rgba(255,255,255,.07), rgba(255,255,255,0) 70%);
  }
  .front__brand {
    position: absolute; left: 0; right: 0; top: 132px; text-align: center;
    font-family: "Montserrat", sans-serif; font-weight: 500;
    font-size: 54px; letter-spacing: 3px; color: #f2f2f2;
  }
  .front__tagline {
    position: absolute; left: 0; right: 0; top: 246px; text-align: center;
    font-family: "Montserrat", sans-serif; font-weight: 400;
    font-size: 12px; letter-spacing: 2px; color: #e6e6e6; text-transform: uppercase;
  }
  /* Back */
  .card--back { top: 470px; background: var(--paper); }
  .back__map {
    position: absolute; left: 40px; top: 30px; width: 586px; height: 250px;
    background: radial-gradient(ellipse at 50% 50%, rgba(157,157,157,.14), rgba(157,157,157,0) 70%);
  }
  .back__brand {
    position: absolute; left: 36px; top: 140px; width: 240px;
    font-family: "Montserrat", sans-serif; font-weight: 700;
    font-size: 30px; line-height: 1.15; color: var(--blue-deep);
  }
  .back__divider {
    position: absolute; left: 300px; top: 80px; width: 2px; height: 150px;
    background: var(--blue-deep);
  }
  .contact { position: absolute; left: 326px; top: 76px; }
  .contact__name {
    font-family: "Montserrat", sans-serif; font-weight: 700;
    font-size: 22px; letter-spacing: 1px; color: var(--blue-deep); text-transform: uppercase;
  }
  .contact__role { font-size: 14px; color: #333; margin-top: 2px; margin-bottom: 12px; }
  .contact__list { list-style: none; }
  .contact__item {
    display: flex; align-items: center; gap: 10px;
    font-size: 14px; line-height: 20px; color: #333;
  }
  .contact__icon { width: 12px; height: 12px; flex: none; }
  .back__rule {
    position: absolute; left: 0; right: 0; top: 300px; height: 2px; background: var(--blue-deep);
  }
  .back__band {
    position: absolute; left: 0; right: 0; top: 306px; bottom: 0;
    background: var(--graphite);
    display: flex; align-items: center; justify-content: center;
    color: #f0f0f0; font-size: 15px; letter-spacing: .3px;
  }
</style>
</head>
<body>

<section class="card card--front">
  <div class="front__map" role="img" aria-label="Faint world map in the background"></div>
  <div class="front__brand">Vantore Global</div>
  <p class="front__tagline">Providing leadership | Delivering success</p>
</section>

<section class="card card--back">
  <div class="back__map" role="img" aria-label="Faint dotted world map in the background"></div>
  <div class="back__brand">Vantore Global</div>
  <div class="back__divider"></div>

  <div class="contact">
    <h1 class="contact__name">Daniel Hale</h1>
    <p class="contact__role">Design Consultant</p>
    <ul class="contact__list">
      <li class="contact__item">
        <svg class="contact__icon" viewBox="0 0 12 12"><rect x="3" y="0.5" width="6" height="11" rx="1" fill="none" stroke="#3276b5" stroke-width="1.2"/><circle cx="6" cy="9.5" r=".7" fill="#3276b5"/></svg>
        555-201-4837
      </li>
      <li class="contact__item">
        <svg class="contact__icon" viewBox="0 0 12 12"><path d="M2.5 1 L4.5 1 L5.2 3.5 L4 4.5 Q5 7 7.5 8 L8.5 6.8 L11 7.5 L11 9.5 Q6 11 2 6 Q1 3 2.5 1Z" fill="#3276b5"/></svg>
        01632 960418 (Brookford)
      </li>
      <li class="contact__item">
        <svg class="contact__icon" viewBox="0 0 12 12"><path d="M2.5 1 L4.5 1 L5.2 3.5 L4 4.5 Q5 7 7.5 8 L8.5 6.8 L11 7.5 L11 9.5 Q6 11 2 6 Q1 3 2.5 1Z" fill="#3276b5"/></svg>
        01632 960527 (Ashcombe)
      </li>
      <li class="contact__item">
        <svg class="contact__icon" viewBox="0 0 12 12"><rect x="0.6" y="2.5" width="10.8" height="7" fill="none" stroke="#3276b5" stroke-width="1.2"/><path d="M0.6 2.5 L6 6.5 L11.4 2.5" fill="none" stroke="#3276b5" stroke-width="1.2"/></svg>
        info@vantoreglobal.com
      </li>
      <li class="contact__item">
        <svg class="contact__icon" viewBox="0 0 12 12"><circle cx="6" cy="6" r="5.2" fill="none" stroke="#3276b5" stroke-width="1.2"/><ellipse cx="6" cy="6" rx="2.2" ry="5.2" fill="none" stroke="#3276b5" stroke-width="1"/><line x1="0.8" y1="6" x2="11.2" y2="6" stroke="#3276b5" stroke-width="1"/></svg>
        www.vantoreglobal.com
      </li>
    </ul>
  </div>

  <div class="back__rule"></div>
  <div class="back__band">Unit 8, The Linden Centre, Mill Lane, Brookford, Herts BR4 2QT</div>
</section>

</body>
</html>
```